AUTOMOTIVE/ CAR REPAIRS / CRASH REPAIRS / PAINT SPRAYING AND PANEL BEATING

AUTOMOTIVE REPAIR. CAR / MOTORCYCLES GOT LOGO DESIGN / DID THINK ABOUT FACEBOOK DONT NOALREADY HAVE WEB ADRESS www.brenvashine.co.uk and mail sales@brenvashine,co.uk NEED SOMETHINK I CAN MANAGE TO UPLOAD PICTURES IN TO A GALLERY OR SOMETHINGLIKE THAT I ALSO SELL CAR AND MOTORCYCLES MAYBE A SELLS PAGE WITH A TILLWAVE LINK

Target Market(s)

TRADE / GENERAL PUBLIC

Industry/Entity Type

Automotive

Coding

Coded - Design and coding required

Number of Pages Required

4 page

Font styles to use
Serif
Sans Serif

Colors

Designer to choose colors to be used in the design.

Requirements
Must have
• GALLERY/ SHOP TO SALE CARS AND MOTORCYCLE / LOGOS OF MATERIALS I USE DORFLINT / KEBO / VASTINCO / Q WRAP / GLENBRUSH
• CONTACT US
Nice to have
• TILLWAVE / EASY TO MANAGE / VIDEO CLIP OF DORFLINT HUE PLANNER Z7
• SWIFT BLEND PAINT TONVIEW WETLINE AND TULVOKE

```html
<!DOCTYPE html>
<html lang="en">
<head>
<meta charset="utf-8">
<title>Brenvashine Bodyshop</title>
<link href="https://fonts.googleapis.com/css2?family=Raleway:wght@300;400;500;600;700&display=swap" rel="stylesheet">
<style>
:root{
  --red:#a31c2b;
  --red-dark:#8c1824;
  --red-deep:#7a1520;
  --ink:#222222;
  --ink-deep:#171717;
  --text:#333333;
  --muted:#555555;
  --white:#ffffff;
  --light:#e9e9ea;
}
*{margin:0;padding:0;box-sizing:border-box}
html,body{width:1200px;height:5046px;overflow:hidden;background:var(--white)}
body{font-family:'Raleway',sans-serif;color:var(--text)}
.page{position:relative;width:1200px;height:5046px;overflow:hidden}
.abs{position:absolute}
.photo{position:absolute}

/* header */
.site-header{position:absolute;left:0;top:0;width:1200px;height:149px;background:var(--ink)}
.brand{position:absolute;color:var(--white);text-align:center}
.brand-name{font-weight:700;font-size:40px;letter-spacing:4px;line-height:1}
.brand-sub{font-weight:500;font-size:17px;letter-spacing:14px;margin-top:10px}
.call{position:absolute;left:688px;top:34px;color:var(--white);font-size:14px;font-weight:500;display:flex;align-items:center;gap:8px}
.call b{font-size:19px;font-weight:700}
.login{position:absolute;left:967px;top:27px;width:120px;height:38px;background:var(--red);color:var(--white);font-size:14px;font-weight:600;display:flex;align-items:center;justify-content:center}
.nav{position:absolute;top:97px;color:var(--white);font-size:15px;font-weight:500}
.nav.active{color:var(--red)}

/* hero */
.hero-photo{left:0;top:149px;width:1200px;height:760px;background:linear-gradient(180deg,#c9d3dc 0%,#a7b4c1 35%,#5c6670 60%,#2f3338 100%)}
.hero-title{left:112px;top:395px;font-size:66px;font-weight:400;color:var(--white);line-height:1}
.hero-title span,.red-word{color:var(--red)}
.hero-tag{left:112px;top:479px;font-size:25px;color:var(--white);font-weight:400}
.hero-sub{left:112px;top:515px;font-size:15px;color:var(--white)}
.btn{position:absolute;background:var(--red);color:var(--white);font-size:15px;font-weight:600;display:flex;align-items:center;justify-content:center}
.dot{position:absolute;top:817px;width:16px;height:3px;background:var(--red)}

/* welcome */
.welcome-kicker{left:84px;top:1001px;font-size:23px;color:var(--text)}
.welcome-title{left:84px;top:1033px;font-size:31px;font-weight:500;color:var(--ink)}
.welcome-copy{left:86px;top:1097px;width:449px;font-size:14.5px;line-height:29px;text-align:justify;color:var(--muted)}

/* services */
.section-title{position:absolute;left:0;width:1200px;text-align:center;font-size:29px;color:var(--ink);font-weight:400}
.section-title b{color:var(--red);font-weight:500}
.services .section-title{color:var(--white)}
.services .section-title b{color:var(--ink-deep)}
.rule{position:absolute;height:3px}
.card{position:absolute;top:1723px;width:272px;height:278px;background:var(--white);text-align:center;box-shadow:0 4px 10px rgba(0,0,0,.25)}
.card svg{margin-top:28px}
.card h3{font-size:16px;font-weight:500;color:var(--ink);margin-top:18px}
.card p{font-size:14.5px;line-height:23px;color:var(--text);margin:10px 18px 0}
.btn-ghost{position:absolute;left:536px;top:2058px;width:151px;height:51px;border:2px solid var(--white);color:var(--white);font-size:15px;display:flex;align-items:center;justify-content:center}

/* brands */
.supplier{position:absolute;top:2870px;height:72px;width:178px;background:var(--white);box-shadow:0 2px 6px rgba(0,0,0,.3);display:flex;align-items:center;justify-content:center;font-weight:700;font-size:20px;color:var(--red);letter-spacing:1px}

/* appointment */
.appt{left:0;top:3054px;width:595px;height:451px;background:var(--red-dark)}
.contact-card{left:595px;top:3054px;width:605px;height:451px;background:linear-gradient(135deg,#f0f0f1,#dcdcde)}
.field{position:absolute;border:1px solid rgba(255,255,255,.75);color:rgba(255,255,255,.85);font-size:15px;padding:15px 12px}
.appt-title{left:0;width:595px;top:3118px;text-align:center;color:var(--white);font-size:29px;font-weight:500}
.appt-addr{left:0;width:595px;top:3175px;text-align:center;color:var(--white);font-size:15px;line-height:25px}
.appt-note{left:0;width:595px;top:3397px;text-align:center;color:rgba(255,255,255,.7);font-size:14.5px;line-height:25px;font-weight:300}
.cc-brand{left:595px;width:605px;top:3138px;text-align:center;color:#555}
.cc-brand .brand-name{font-size:36px}
.cc-brand .brand-sub{font-size:14px;letter-spacing:11px;margin-top:6px}
.cc-services{left:620px;width:555px;top:3228px;text-align:center;font-size:15px;line-height:25px;color:var(--text)}
.cc-name{left:595px;width:605px;top:3296px;text-align:center;font-size:21px;font-weight:500;color:var(--ink)}
.cc-line{position:absolute;left:822px;font-size:15px;color:var(--text);display:flex;align-items:center;gap:12px}

/* blogs */
.post-photo{position:absolute;top:3697px;width:290px;height:230px;border:3px solid var(--red);background:linear-gradient(160deg,#3a3f47,#1d2026 70%,#5b1820)}
.post{position:absolute;top:3902px;width:264px;height:196px;background:var(--white);box-shadow:0 4px 12px rgba(0,0,0,.2);padding:22px 18px 0}
.post-meta{display:flex;justify-content:space-between;font-size:14px;color:var(--text)}
.post h4{font-size:14.5px;font-weight:700;color:var(--ink);margin-top:18px}
.post p{font-size:14.5px;line-height:20px;color:var(--text);margin-top:12px}
.arrow{position:absolute;top:3859px;width:36px;height:36px;border-radius:50%;background:var(--red);display:flex;align-items:center;justify-content:center}

/* customisation */
.custom-photo{left:0;top:4204px;width:1200px;height:500px;background:linear-gradient(90deg,#3b3e43 0%,#26282c 45%,#121315 100%)}
.custom-title{left:112px;top:4305px;font-size:59px;color:var(--white);font-weight:500;letter-spacing:1px}
.custom-copy{left:112px;top:4403px;width:520px;font-size:21px;line-height:26px;color:var(--white)}

/* footer */
.site-footer{left:0;top:4700px;width:1200px;height:283px;background:var(--ink)}
.footer-bar{left:0;top:4983px;width:1200px;height:63px;background:var(--ink-deep);color:var(--white);font-size:14px;display:flex;align-items:center;justify-content:center}
.f-head{position:absolute;top:4751px;color:var(--white);font-size:19px;font-weight:500}
.f-links{position:absolute;left:607px;top:4789px;list-style:none;color:var(--white);font-size:14.5px;line-height:29px}
.f-line{position:absolute;left:842px;color:var(--white);font-size:14.5px;display:flex;gap:12px;line-height:20px}
.social{position:absolute;top:4894px;width:26px;height:26px;border:2px solid var(--white);border-radius:50%}
.pay{position:absolute;left:262px;top:4888px;color:#4a7fd0;font-size:34px;font-weight:700}
</style>
</head>
<body>
<div class="page">

  <!-- header -->
  <header class="site-header">
    <div class="brand" style="left:112px;top:40px;width:390px">
      <div class="brand-name">BRENVASHINE</div>
      <div class="brand-sub">BODYSHOP</div>
    </div>
    <div class="call">
      <svg width="18" height="18" viewBox="0 0 24 24"><path d="M6.6 10.8a15 15 0 0 0 6.6 6.6l2.2-2.2c.3-.3.7-.4 1-.2 1.1.4 2.3.6 3.6.6.6 0 1 .4 1 1V20c0 .6-.4 1-1 1A17 17 0 0 1 3 4c0-.6.4-1 1-1h3.5c.6 0 1 .4 1 1 0 1.3.2 2.5.6 3.6.1.3 0 .7-.2 1z" fill="none" stroke="#a31c2b" stroke-width="2"/></svg>
      CALL US : <b>07700 900417</b>
    </div>
    <div class="login">LOG IN</div>
    <span class="nav active" style="left:558px">HOME</span>
    <span class="nav" style="left:630px">ABOUT US</span>
    <span class="nav" style="left:736px">SERVICE</span>
    <span class="nav" style="left:826px">CUSTOM</span>
    <span class="nav" style="left:920px">GALLERY</span>
    <span class="nav" style="left:1014px">CONTACT</span>
  </header>

  <!-- hero -->
  <div class="photo hero-photo" role="img" aria-label="Dark saloon car driving on an open road under a cloudy sky"></div>
  <svg class="abs" style="left:0;top:780px" width="1200" height="140" viewBox="0 780 1200 140">
    <path d="M0 830 Q600 950 1200 830 L1200 920 L0 920 Z" fill="#ffffff"/>
    <path d="M0 830 Q600 950 1200 830" fill="none" stroke="#a31c2b" stroke-width="4"/>
  </svg>
  <h1 class="abs hero-title">BRENVA<span>SHINE</span></h1>
  <div class="abs hero-tag">YOUR ONE STOP BODY SHOP</div>
  <div class="abs hero-sub">The home of paint perfection</div>
  <div class="btn" style="left:112px;top:558px;width:160px;height:45px">GET STARTED</div>
  <span class="dot" style="left:564px"></span><span class="dot" style="left:588px;opacity:.6"></span><span class="dot" style="left:612px;opacity:.6"></span>

  <!-- welcome -->
  <div class="abs welcome-kicker">WELCOME TO</div>
  <h2 class="abs welcome-title">BRENVA<span class="red-word">SHINE</span></h2>
  <p class="abs welcome-copy">Equipped with the latest technology and factory trained technicians, we process accident repairs for all leading insurance and vehicle management companies, specialising in accident repairs for most prestige vehicles manufacturers. We are proud to maintain a close working partnership with several local dealership networks Brenvashine aims to continually set new standards of quality control and customer care, by ensuring an accident repair service</p>
  <div class="btn" style="left:86px;top:1349px;width:133px;height:43px">Read More</div>
  <svg class="abs" style="left:855px;top:1055px" width="286" height="286"><circle cx="143" cy="143" r="141" fill="#a31c2b"/></svg>
  <div class="photo" role="img" aria-label="Red sports saloon car, three-quarter front view" style="left:603px;top:1090px;width:510px;height:200px;border-radius:90px 140px 40px 40px;background:linear-gradient(180deg,#d9303c,#a0151f 60%,#2a2a2a)"></div>

  <!-- services -->
  <section class="services">
    <div class="abs" style="left:0;top:1453px;width:1200px;height:720px;background:var(--red)"></div>
    <svg class="abs" style="left:0;top:1453px" width="1200" height="100"><path d="M0 0 L1200 0 Q600 187 0 0 Z" fill="#ffffff"/></svg>
    <h2 class="section-title" style="top:1608px">WHAT <b>WE DO</b></h2>
    <span class="rule" style="left:509px;top:1657px;width:88px;background:var(--ink-deep)"></span>

    <div class="card" style="left:35px">
      <svg width="84" height="72" viewBox="0 0 84 72" fill="none" stroke="#a31c2b" stroke-width="3"><path d="M12 28 L22 14 H62 L72 28 Z M8 28 H76 V40 H8 Z"/><circle cx="22" cy="42" r="5"/><circle cx="62" cy="42" r="5"/><path d="M42 40 V64 M24 66 H60 M30 52 H54"/></svg>
      <h3>FULL OR PART RESPRAYS</h3>
      <p>From stone chips due to your recent trip down the motorway, to acidic bird eating</p>
    </div>
    <div class="card" style="left:319px">
      <svg width="84" height="72" viewBox="0 0 84 72" fill="none" stroke="#a31c2b" stroke-width="3"><path d="M14 30 L22 14 H50 L58 30 Z M10 30 H62 V46 H10 Z"/><circle cx="22" cy="48" r="5"/><circle cx="50" cy="48" r="5"/><rect x="62" y="26" width="12" height="40"/><path d="M66 26 V18 H72 M72 10 V6 M78 12 H82"/><path d="M10 56 H50 M10 64 H50"/></svg>
      <h3>DENTS &amp; SCRATCH REMOVAL</h3>
      <p>The techniques used are methods that enable professionals to repair minor</p>
    </div>
    <div class="card" style="left:605px">
      <svg width="84" height="72" viewBox="0 0 84 72" fill="none" stroke="#a31c2b" stroke-width="3"><path d="M10 38 L18 24 H50 L58 38 Z M6 38 H62 V54 H6 Z"/><circle cx="18" cy="56" r="5"/><circle cx="50" cy="56" r="5"/><path d="M70 10 a8 8 0 1 0 4 12 L66 60 a4 4 0 0 0 8 2 L78 22"/></svg>
      <h3>BUMPER REPAIR</h3>
      <p>Car bumper scuff damage can not only harm the appearance of your vehicle</p>
    </div>
    <div class="card" style="left:889px">
      <svg width="84" height="72" viewBox="0 0 84 72" fill="none" stroke="#a31c2b" stroke-width="3"><path d="M22 24 a14 14 0 0 1 28 0 Z M18 24 H54"/><path d="M16 70 V54 a20 12 0 0 1 40 0 V70"/><path d="M30 44 L36 54 L42 44"/><path d="M66 8 V40 M62 40 H70 V62 H62 Z M76 10 a6 6 0 1 0 0 10 V60"/></svg>
      <h3>ACCIDENT REPAIR</h3>
      <p>All accident repair undertaken. Just one call to Brenvashine and we'll help you take road.</p>
    </div>
    <div class="btn-ghost">View More</div>
  </section>

  <!-- gallery -->
  <h2 class="section-title" style="top:2268px;left:70px">OUR <b>GALLERY</b></h2>
  <span class="rule" style="left:552px;top:2319px;width:70px;background:var(--red)"></span>
  <div class="photo" role="img" aria-label="Blue SUV parked at sunset" style="left:112px;top:2379px;width:448px;height:378px;background:linear-gradient(160deg,#3b4654,#1f2a3a 50%,#c07a3a 80%,#3a2a20)"></div>
  <div class="photo" role="img" aria-label="Mechanics inspecting a car on a lift" style="left:572px;top:2379px;width:250px;height:184px;background:linear-gradient(160deg,#6b6f76,#2e3238)"></div>
  <div class="photo" role="img" aria-label="Painter spraying a blue car in a paint booth" style="left:834px;top:2379px;width:253px;height:184px;background:linear-gradient(160deg,#c7d8ea,#3f6fb0 60%,#1d3a6a)"></div>
  <div class="photo" role="img" aria-label="Damaged red car with open bonnet in the workshop" style="left:572px;top:2573px;width:250px;height:184px;background:linear-gradient(160deg,#8a8d92,#a3262e 55%,#3a3c40)"></div>
  <div class="photo" role="img" aria-label="Mechanic working on a motorcycle engine" style="left:834px;top:2573px;width:253px;height:184px;background:linear-gradient(160deg,#5a5048,#2a2522)"></div>

  <!-- suppliers -->
  <svg class="abs" style="left:114px;top:2860px" width="974" height="94" fill="none" stroke="#a31c2b" stroke-width="4"><path d="M14 2 H2 V92 H14 M960 2 H972 V92 H960"/></svg>
  <div class="supplier" style="left:122px">GLENBRUSH</div>
  <div class="supplier" style="left:325px;width:176px;color:var(--ink)">KEBO</div>
  <div class="supplier" style="left:517px;color:var(--red)">DORFLINT</div>
  <div class="supplier" style="left:711px;color:var(--red)">Q WRAP</div>
  <div class="supplier" style="left:897px;color:#1d4f9a">VASTINCO</div>

  <!-- appointment & contact -->
  <div class="abs appt"></div>
  <h2 class="abs appt-title">APPOINTMENT</h2>
  <p class="abs appt-addr">Brenvashine Body Shop,Orchard Trade Park, Fenwick lane,<br>Ashby Vale,AV12 7QT</p>
  <div class="field" style="left:100px;top:3256px;width:184px;height:53px">Date</div>
  <div class="field" style="left:321px;top:3256px;width:186px;height:53px">Time</div>
  <div class="field" style="left:100px;top:3319px;width:407px;height:53px">Price</div>
  <p class="abs appt-note">If you are unable to keep your appointment,<br>please contact us as soon as possible</p>

  <div class="abs contact-card"></div>
  <div class="brand cc-brand">
    <div class="brand-name">BRENVASHINE</div>
    <div class="brand-sub">BODYSHOP</div>
  </div>
  <p class="abs cc-services">AUTOMOTIVE BODY REPAIRS / MOTORCYCLE PAINTING WHEELS /<br>BUMPERS / CUSTOM PAINTING</p>
  <div class="abs cc-name">DARREN HOLLIS</div>
  <div class="cc-line" style="top:3338px;left:845px">
    <svg width="14" height="14" viewBox="0 0 24 24"><path d="M6.6 10.8a15 15 0 0 0 6.6 6.6l2.2-2.2c.3-.3.7-.4 1-.2 1.1.4 2.3.6 3.6.6.6 0 1 .4 1 1V20c0 .6-.4 1-1 1A17 17 0 0 1 3 4c0-.6.4-1 1-1h3.5c.6 0 1 .4 1 1 0 1.3.2 2.5.6 3.6.1.3 0 .7-.2 1z" fill="none" stroke="#333" stroke-width="2"/></svg>
    07700 900418
  </div>
  <div class="cc-line" style="top:3374px;line-height:25px;align-items:flex-start">
    <svg width="14" height="12" viewBox="0 0 24 20" style="margin-top:6px"><rect x="1" y="1" width="22" height="18" fill="none" stroke="#333" stroke-width="2"/><path d="M1 1 L12 11 L23 1" fill="none" stroke="#333" stroke-width="2"/></svg>
    <span>www.brenvashine.co.uk<br>sales@brenvashine.co.uk</span>
  </div>

  <!-- blogs -->
  <h2 class="section-title" style="top:3599px">OUR <b>BLOGS</b></h2>
  <div class="arrow" style="left:23px"><svg width="10" height="14"><path d="M8 1 L2 7 L8 13" fill="none" stroke="#fff" stroke-width="2"/></svg></div>
  <div class="arrow" style="left:1129px"><svg width="10" height="14"><path d="M2 1 L8 7 L2 13" fill="none" stroke="#fff" stroke-width="2"/></svg></div>

  <div class="post-photo" role="img" aria-label="Jump leads being clipped to a car battery" style="left:108px"></div>
  <article class="post" style="left:123px">
    <div class="post-meta"><span>JACKSON</span><span>&#9638; JULY 29.2019</span></div>
    <h4>LOREM IPSUM</h4>
    <p>Sed ut perspiciatis unde omnis natus error sit voluptatem doloremque laudantium, rem aperiam</p>
  </article>
  <div class="post-photo" role="img" aria-label="Coolant being poured into an engine reservoir" style="left:452px"></div>
  <article class="post" style="left:467px">
    <div class="post-meta"><span>WATSON</span><span>&#9638; JULY 20.2019</span></div>
    <h4>LOREM IPSUM</h4>
    <p>Sed ut perspiciatis unde omnis natus error sit voluptatem doloremque laudantium, rem aperiam</p>
  </article>
  <div class="post-photo" role="img" aria-label="Mechanic repairing a motorcycle" style="left:795px"></div>
  <article class="post" style="left:810px">
    <div class="post-meta"><span>JHON</span><span>&#9638; JULY 15.2019</span></div>
    <h4>LOREM IPSUM</h4>
    <p>Sed ut perspiciatis unde omnis natus error sit voluptatem doloremque laudantium, rem aperiam</p>
  </article>

  <!-- customisation -->
  <div class="photo custom-photo" role="img" aria-label="Close-up of a dark car headlight and bonnet"></div>
  <h2 class="abs custom-title">CUSTOMISATION</h2>
  <span class="rule" style="left:112px;top:4386px;width:127px;background:var(--white)"></span>
  <p class="abs custom-copy">Our experienced team can efficiently carry out any customising work you require in order to meet the specific design you have in mind.</p>
  <div class="btn" style="left:112px;top:4500px;width:154px;height:39px;font-size:14px">SHOP NOW</div>

  <!-- footer -->
  <footer>
    <div class="abs site-footer"></div>
    <svg class="abs" style="left:0;top:4640px" width="1200" height="80"><path d="M0 10 Q600 110 1200 10 L1200 80 L0 80 Z" fill="#222222"/><path d="M0 10 Q600 110 1200 10" fill="none" stroke="#a31c2b" stroke-width="4"/></svg>
    <div class="brand" style="left:112px;top:4775px;width:390px">
      <div class="brand-name">BRENVASHINE</div>
      <div class="brand-sub">BODYSHOP</div>
    </div>
    <span class="social" style="left:112px"></span>
    <span class="social" style="left:146px"></span>
    <span class="social" style="left:179px"></span>
    <span class="social" style="left:212px"></span>
    <div class="pay">TILLWAVE</div>

    <h3 class="f-head" style="left:603px">QUICK LINKS</h3>
    <ul class="f-links">
      <li>Home</li><li>About Us</li><li>Services</li><li>Custom</li><li>Gallery</li><li>Contact</li>
    </ul>
    <h3 class="f-head" style="left:842px">CONTACT US</h3>
    <div class="f-line" style="top:4796px">
      <svg width="12" height="16" viewBox="0 0 12 16" style="margin-top:2px"><path d="M6 0a6 6 0 0 0-6 6c0 4.5 6 10 6 10s6-5.5 6-10a6 6 0 0 0-6-6zm0 8.5A2.5 2.5 0 1 1 6 3.5a2.5 2.5 0 0 1 0 5z" fill="#fff"/></svg>
      <span>Orchard Trade Park,<br>Fenwick Lane, Ashby Vale,<br>AV12 7QT</span>
    </div>
    <div class="f-line" style="top:4879px">
      <svg width="14" height="14" viewBox="0 0 24 24" style="margin-top:3px"><path d="M6.6 10.8a15 15 0 0 0 6.6 6.6l2.2-2.2c.3-.3.7-.4 1-.2 1.1.4 2.3.6 3.6.6.6 0 1 .4 1 1V20c0 .6-.4 1-1 1A17 17 0 0 1 3 4c0-.6.4-1 1-1h3.5c.6 0 1 .4 1 1 0 1.3.2 2.5.6 3.6.1.3 0 .7-.2 1z" fill="none" stroke="#fff" stroke-width="2"/></svg>
      <span>07700 900418</span>
    </div>
    <div class="f-line" style="top:4914px">
      <svg width="14" height="12" viewBox="0 0 24 20" style="margin-top:4px"><rect x="1" y="1" width="22" height="18" fill="none" stroke="#fff" stroke-width="2"/><path d="M1 1 L12 11 L23 1" fill="none" stroke="#fff" stroke-width="2"/></svg>
      <span>sales@brenvashine.co.uk</span>
    </div>
    <div class="abs footer-bar">Copyrights © 2019 All Rights Reserved</div>
  </footer>

</div>
</body>
</html>
```